Letterhead for Conveyancing Company

Use existing logo to create a letterhead for a conveyancing company. Must be able to be used in Microsoft Word. Easy to read and professional.
Contact information to be at the bottom.
Bright Oak Conveyancing Pty Ltd
ACN 621 984 736PO Box 535 Campbelltown SA 5074
Mobile - 0461739286
Web address - www.brightoakconveyancing.com.au

Requirements
Must have
• Logo and contact details.
• Simple and professional.

```html
<!DOCTYPE html>
<html lang="en">
<head>
<meta charset="utf-8">
<title>Bright Oak Conveyancing – Letterhead</title>
<link href="https://fonts.googleapis.com/css2?family=Roboto:wght@400;500;700&family=Allura&display=swap" rel="stylesheet">
<style>
  :root {
    --backdrop: #4d4a49;
    --paper: #fafafa;
    --brand-pink: #e0449a;
    --brand-grey: #7f7f7f;
    --text: #555555;
    --text-strong: #4a4a4a;
    --ink-blue: #2e4f86;
  }
  * { margin: 0; padding: 0; box-sizing: border-box; }
  html, body { width: 1062px; height: 1200px; overflow: hidden; }
  body {
    background: var(--backdrop);
    font-family: "Roboto", Arial, sans-serif;
    color: var(--text);
    position: relative;
  }
  .letterhead {
    position: absolute;
    left: 200px; top: 132px;
    width: 662px; height: 936px;
    background: var(--paper);
    overflow: hidden;
  }
  .swoosh { position: absolute; left: 0; top: 0; width: 662px; height: 936px; }
  .brand-name {
    position: absolute; left: 41px; top: 84px;
    font-size: 30px; line-height: 32px; font-weight: 700;
    color: var(--brand-pink);
  }
  .letter-date { position: absolute; left: 41px; top: 220px; font-size: 11px; }
  .recipient { position: absolute; left: 41px; top: 264px; font-size: 11px; line-height: 15px; }
  .recipient strong { color: var(--text-strong); font-weight: 500; }
  .salutation { position: absolute; left: 41px; top: 355px; font-size: 11px; }
  .letter-body {
    position: absolute; left: 41px; top: 384px; width: 579px;
    font-size: 10.6px; line-height: 15px; text-align: justify;
  }
  .letter-body p { margin-bottom: 15px; }
  .sign-off { position: absolute; left: 41px; top: 731px; font-size: 11px; }
  .sign-off .signer { color: var(--text-strong); font-weight: 500; }
  .sign-off .signature {
    font-family: "Allura", cursive; font-size: 30px; color: var(--ink-blue);
    margin: 2px 0 0 -14px; line-height: 34px;
  }
  .sign-off .role { margin-top: 4px; }
  .contact { position: absolute; right: 41px; top: 808px; text-align: right; font-size: 11px; }
  .contact .company { color: var(--brand-pink); font-weight: 500; font-size: 13.5px; margin-bottom: 14px; }
  .contact .line { display: flex; justify-content: flex-end; align-items: center; gap: 6px; height: 17px; }
  .contact svg { width: 9px; height: 9px; fill: var(--brand-pink); }
  .contact .label { color: var(--brand-pink); margin-left: 8px; }
</style>
</head>
<body>
  <main class="letterhead">
    <svg class="swoosh" viewBox="0 0 662 936" aria-hidden="true">
      <path d="M25 0 L662 0 L662 47 C480 22 260 6 25 0 Z" fill="var(--brand-pink)"/>
      <path d="M195 14 C400 26 560 48 662 64 L662 79 C560 58 400 34 195 14 Z" fill="var(--brand-grey)"/>
      <path d="M0 856 C150 872 330 898 465 920 C320 908 150 893 0 882 Z" fill="var(--brand-grey)"/>
      <path d="M0 887 C200 903 440 922 662 933 L662 936 L0 936 Z" fill="var(--brand-pink)"/>
    </svg>

    <div class="brand-name">Bright Oak<br>Conveyancing</div>

    <div class="letter-date">30/20/2016</div>

    <address class="recipient" style="font-style:normal">
      <strong>Mr. XYZ Smith</strong><br>
      123, Street No. 123,<br>
      City Name<br>
      Pincode-123456
    </address>

    <div class="salutation">Dear Sir,</div>

    <section class="letter-body">
      <p>Lorem Ipsum is simply dummy text of the printing and typesetting industry. Lorem Ipsum has been the industry's standard dummy text ever since the 1500s, when an unknown printer took a galley of type and scrambled it to make a type specimen book. It has survived not only five centuries, but also the leap into electronic typesetting, remaining essentially unchanged. It was popularised in the 1960s with the release of Letraset sheets containing Lorem Ipsum passages, and more recently with desktop publishing software like Aldus PageMaker including versions of Lorem Ipsum.</p>
      <p>Lorem Ipsum is simply dummy text of the printing and typesetting industry. Lorem Ipsum has been the industry's standard dummy text ever since the 1500s, when an unknown printer took a galley of type and scrambled it to make a type specimen book. It has survived not only five centuries, but also the leap into electronic typesetting, remaining essentially unchanged. It was popularised in the 1960s with the release of Letraset sheets containing Lorem Ipsum passages, and more recently with desktop publishing software like Aldus PageMaker including versions of Lorem Ipsum.</p>
      <p>Lorem Ipsum is simply dummy text of the printing and typesetting industry. Lorem Ipsum has been the industry's standard dummy text ever since the 1500s, when an unknown printer took a galley of type and scrambled it to make a type specimen book.</p>
      <p>Lorem Ipsum is simply dummy text of the printing and typesetting industry. Lorem Ipsum has been the industry's standard dummy text ever since the 1500s, when an unknown printer took a galley of type and scrambled it to make a type specimen book.</p>
    </section>

    <div class="sign-off">
      <div class="signer">Your Name</div>
      <div class="signature">Your Signature</div>
      <div class="role">CEO &nbsp;|&nbsp; Owner</div>
    </div>

    <footer class="contact">
      <div class="company">Bright Oak Conveyancing Pty Ltd</div>
      <div class="line">
        <svg viewBox="0 0 10 10"><path d="M1 3 C1 1.5 9 1.5 9 3 L7.5 4 L6.5 3 L3.5 3 L2.5 4 Z M2.5 5 L7.5 5 L8.5 9 L1.5 9 Z"/></svg>
        <span>046 173 9286</span>
        <span class="label">#&nbsp; ACN</span><span>583 217 469</span>
      </div>
      <div class="line">
        <svg viewBox="0 0 10 10"><circle cx="5" cy="5" r="4.3" fill="none" stroke="var(--brand-pink)" stroke-width="1"/><path d="M0.7 5 H9.3 M5 0.7 V9.3" stroke="var(--brand-pink)" stroke-width="0.8"/></svg>
        <span>www.brightoakconveyancing.com.au</span>
      </div>
      <div class="line">
        <svg viewBox="0 0 10 10"><path d="M5 0.5 C2.5 0.5 1.5 2.3 1.5 3.8 C1.5 6 5 9.5 5 9.5 C5 9.5 8.5 6 8.5 3.8 C8.5 2.3 7.5 0.5 5 0.5 Z M5 2.6 A1.2 1.2 0 1 0 5 5 A1.2 1.2 0 1 0 5 2.6 Z" fill-rule="evenodd"/></svg>
        <span>PO Box 871 Marlowdale SA 5096</span>
      </div>
    </footer>
  </main>
</body>
</html>
```